Label or packaging Design for Hair Care Line

Dear Designer,
We are Pelvoro, a brand known for our premium hairstyling tools, and we are excited to expand into hair care. We are currently looking for a talented designer to create the label designs for our entire luxury hair care line.
This project is crucial in establishing our visual identity in the hair care market, and we aim to position ourselves alongside premium brands such as TKW, Fendrick Hair Atelier, and Morvi.
Project Scope
We need a cohesive label design for our hair care line, which includes:
5 products (e.g., shampoo, conditioner, hair oil, styling cream, and a hair mask).
The designs should include:
Front label: Highlighting the product name, key features, and branding.
Our goal is to achieve a design that communicates premium luxury with a touch of professionalism. Below are the specific guidelines to help you align with our vision:
Style and Inspiration
Think of brands like TKW, Fendrick Hair Atelier, and Morvi.
Luxury and Minimalism: Clean lines, sophisticated typography, and an elegant color palette.
Subtle femininity: premium finishes like metallic accents (gold, silver, or rose gold).
Brand Personality
Premium: Reflecting high quality and exclusivity.
Modern & Professional: Appealing to a refined, professional audience but also suitable for lifestyle-oriented customers.
Warm & Empowering: A brand that celebrates confidence and individuality.
Color Palette
Neutral tones like black, white, accented with metallics (gold or silver) for a luxurious feel.
Colors that feel timeless and elegant rather than trendy or overly bright.
Typography
Use clean, modern fonts (preferably sans-serif or serif for a refined look).
Clear and legible for all product details while maintaining a high-end aesthetic.
Materials and Finishes
Packaging Shape
The label designs should suit a variety of bottle and jar shapes (e.g., cylindrical, flat, or rounded).
Keep scalability in mind so the identity remains consistent across different products.
Deliverables
To understand the aesthetic we are aiming for, here are some brands to use as inspiration:
TKW: For its minimalistic and modern approach.
Fendrick Hair Atelier: For its combination of luxury and professional appeal.
Morvi: For its soft femininity and lifestyle branding.
we would like to see your designs applied to a variety of packaging types to get an overall impression of how the brand identity works across different product formats. This includes:
A squeeze bottle (e.g., for styling creams or conditioners).
A glass bottle with a dropper (e.g., for a luxurious hair oil).
A shampoo/conditioner bottle (standard pump or flip-top cap).
A spray bottle (e.g., for leave-in treatments or heat protectors).
By creating designs for these different packaging types, we can better evaluate how cohesive and versatile the brand identity will be across the entire product line.

Updates
As you may have noticed from the designs, they don’t quite align with our briefing. The look needs to be clean and professional, similar to Fendrick, TKW, and the other examples we provided. Please address this, and we’ll check it!

Target Market(s)
europe and us
Font styles to use
Other font styles liked:
- century gothic

Look and feel

```html
<!DOCTYPE html>
<html lang="en">
<head>
<meta charset="utf-8">
<title>Pelvoro Hair Shampoo – Product Range</title>
<link rel="stylesheet" href="https://fonts.googleapis.com/css2?family=Questrial&family=Bodoni+Moda:wght@500&family=Montserrat:wght@500&display=swap">
<style>
  :root {
    --backdrop: #eeeeee;
    --label: #ffffff;
    --bottle: #141414;
    --bottle-edge: #2a2a2a;
    --nozzle: #8a8a8a;
    --ink: #1a1a1a;
    --ink-soft: #5a5a5a;
    --shadow: rgba(0, 0, 0, 0.10);
  }
  * { margin: 0; padding: 0; box-sizing: border-box; }
  html, body { width: 1200px; height: 801px; overflow: hidden; }
  body { background: var(--backdrop); position: relative; }

  .lineup { position: absolute; inset: 0; width: 1200px; height: 801px; }
  .bottle-body, .bottle-cap { fill: var(--bottle); }
  .bottle-cap-tier { fill: var(--bottle-edge); }
  .label-face { fill: var(--label); }
  .spray-nozzle { fill: var(--nozzle); }
  .ground-shadow { fill: var(--shadow); }

  .label-text {
    position: absolute;
    text-align: center;
    color: var(--ink);
  }
  .label-text--large  { left: 392px; width: 154px; top: 438px; }
  .label-text--medium { left: 565px; width: 117px; top: 474px; }
  .label-text--small  { left: 700px; width: 117px; top: 531px; }

  .brand-name {
    font-family: "Questrial", "Century Gothic", sans-serif;
    font-weight: 400;
    letter-spacing: 0.02em;
    line-height: 1;
  }
  .product-name {
    font-family: "Bodoni Moda", serif;
    font-weight: 500;
    letter-spacing: 0.06em;
    text-transform: uppercase;
    line-height: 1.1;
  }
  .claim {
    font-family: "Montserrat", sans-serif;
    font-weight: 500;
    text-transform: uppercase;
    color: var(--ink-soft);
    letter-spacing: 0.06em;
    line-height: 1.5;
    margin: 0 auto;
  }

  .label-text--large .brand-name   { font-size: 32px; }
  .label-text--large .product-name { font-size: 11.5px; margin-top: 4px; }
  .label-text--large .claim        { font-size: 4.2px; width: 108px; margin-top: 5px; }

  .label-text--medium .brand-name   { font-size: 24px; }
  .label-text--medium .product-name { font-size: 8.6px; margin-top: 3px; }
  .label-text--medium .claim        { font-size: 3.3px; width: 82px; margin-top: 4px; }

  .label-text--small .brand-name   { font-size: 24px; }
  .label-text--small .product-name { font-size: 8.4px; margin-top: 3px; }
  .label-text--small .claim        { font-size: 3.2px; width: 80px; margin-top: 4px; }
</style>
</head>
<body>
  <svg class="lineup" viewBox="0 0 1200 801" aria-hidden="true">
    <ellipse class="ground-shadow" cx="604" cy="712" rx="250" ry="6"/>

    <!-- pump bottle -->
    <g class="bottle bottle--pump">
      <rect class="bottle-cap" x="452" y="148" width="14" height="64"/>
      <path class="bottle-cap" d="M438 130 H530 L541 133 V142 L528 140 H500 V154 H438 Z"/>
      <rect class="bottle-cap" x="434" y="208" width="48" height="58" rx="3"/>
      <path class="bottle-body" d="M392 710 V286 Q392 264 414 264 H524 Q546 264 546 286 V710 Z"/>
      <rect class="label-face" x="392" y="288" width="154" height="388"/>
    </g>

    <!-- medium spray bottle -->
    <g class="bottle bottle--spray">
      <rect class="bottle-cap" x="606" y="190" width="34" height="38" rx="3"/>
      <circle class="spray-nozzle" cx="623" cy="198" r="3"/>
      <rect class="bottle-cap-tier" x="597" y="226" width="52" height="38" rx="3"/>
      <rect class="bottle-cap" x="590" y="262" width="64" height="46" rx="3"/>
      <path class="bottle-body" d="M565 710 V324 Q565 306 583 306 H664 Q682 306 682 324 V710 Z"/>
      <rect class="label-face" x="565" y="330" width="117" height="346"/>
    </g>

    <!-- small spray bottle -->
    <g class="bottle bottle--spray">
      <rect class="bottle-cap" x="741" y="283" width="34" height="37" rx="3"/>
      <circle class="spray-nozzle" cx="758" cy="291" r="3"/>
      <rect class="bottle-cap-tier" x="732" y="318" width="52" height="36" rx="3"/>
      <rect class="bottle-cap" x="725" y="352" width="66" height="46" rx="3"/>
      <path class="bottle-body" d="M700 710 V414 Q700 396 718 396 H799 Q817 396 817 414 V710 Z"/>
      <rect class="label-face" x="700" y="416" width="117" height="260"/>
    </g>
  </svg>

  <section class="label-text label-text--large">
    <p class="brand-name">Pelvoro</p>
    <p class="product-name">Hair Shampoo</p>
    <p class="claim">Leaves hair smooth, rejuvenated and restored without looking greasy</p>
  </section>

  <section class="label-text label-text--medium">
    <p class="brand-name">Pelvoro</p>
    <p class="product-name">Hair Shampoo</p>
    <p class="claim">Leaves hair smooth, rejuvenated and restored without looking greasy</p>
  </section>

  <section class="label-text label-text--small">
    <p class="brand-name">Pelvoro</p>
    <p class="product-name">Hair Shampoo</p>
    <p class="claim">Leaves hair smooth, rejuvenated and restored without looking greasy</p>
  </section>
</body>
</html>
```